Varentoria Business Card and Letter Head

We are a leadership assessment consultancy based in Sydney, Australia. We help executive-level decison-makers select leaders for more senior level roles in corporate and government organisations. Our methodology is based on the latest research from the field of neuroscience.
We need a business card design and matching letter head that presents our company, Varentoria, as a:
1. trusted adviser to senior executive-level decison makers
2. niche consultancy who are experts in the field of assessing leadership talent
3. results-focused solution provider who balance scientific methods with pragmatic solutions
The following company details should be used in all designs:
Company Name: Varentoria
Details (for business card):
Derek Hanford
Prime Capacity Officer
Level 17, Marlow Tower
7 Marlow Square
Sydney, NSW 2090 Australia
Phone: 1300 582 714
Mobile: 0412 637 258
Email: derek.hanford@varentoria-example.com.au
Website: varentoria-example.com.au
I have attached the logo for Varentoria (for both a white and black background) - your business card and letter head designs must incoporate this logo and colour scheme.
Thanks for your interest in this project, I'm looking forward to receiving your ideas.
Regards,
Derek
Target Market(s)
Executive-level decison-makers in corporate and government organisations (e.g., CEO, VP, Head of Human Resources)
Industry/Entity Type
Leadership
Look and feel

```html
<!DOCTYPE html>
<html lang="en">
<head>
<meta charset="utf-8">
<title>Varentoria Business Card</title>
<link rel="stylesheet" href="https://fonts.googleapis.com/css2?family=Open+Sans:wght@300;400;600;700&display=swap">
<style>
  :root {
    --backdrop: #e9e6e2;
    --card: #ffffff;
    --ink: #3a3a3d;
    --ink-soft: #555558;
    --accent: #c0272d;
    --accent-dark: #8e1a1e;
    --strip-black: #151515;
  }
  * { margin: 0; padding: 0; box-sizing: border-box; }
  html, body {
    width: 1200px; height: 427px; overflow: hidden;
    background: var(--backdrop);
    font-family: "Open Sans", Arial, sans-serif;
  }
  .canvas { position: relative; width: 1200px; height: 427px; }

  .card {
    position: absolute; top: 65px; height: 297px;
    background: var(--card); border-radius: 22px; overflow: hidden;
    box-shadow: 0 3px 10px rgba(0,0,0,0.18);
  }
  .card--front { left: 70px; width: 522px; }
  .card--back { left: 610px; width: 520px; }

  .edge-strip {
    position: absolute; top: 0; right: 0; width: 27px; height: 100%;
    background: linear-gradient(180deg, var(--accent) 0%, var(--accent-dark) 38%, var(--strip-black) 62%, var(--strip-black) 100%);
  }

  .brand { position: absolute; left: 33px; top: 28px; display: flex; align-items: center; }
  .brand__mark { width: 56px; height: 56px; background: var(--ink); margin-right: 48px; }
  .brand__name { font-size: 50px; font-weight: 700; color: var(--ink); letter-spacing: -1.5px; line-height: 1; }
  .tagline {
    position: absolute; left: 137px; top: 89px;
    font-size: 16px; letter-spacing: 0.5px; color: var(--ink-soft); font-weight: 300;
    white-space: nowrap;
  }

  .person { position: absolute; left: 0; width: 495px; top: 141px; text-align: center; }
  .person__name { font-size: 18px; color: var(--accent); letter-spacing: 0.3px; line-height: 24px; }
  .person__role { font-size: 12px; color: var(--ink); margin-top: 2px; }

  .contact, .address {
    position: absolute; top: 207px; font-size: 12px; line-height: 17px; color: var(--ink);
    list-style: none; white-space: nowrap;
  }
  .contact { left: 33px; }
  .contact__label { color: var(--accent); }
  .address { left: 320px; }
  .website {
    position: absolute; left: 33px; top: 265px;
    font-size: 11px; font-weight: 700; letter-spacing: 1.2px; color: var(--ink);
  }

  .back-brand {
    position: absolute; left: 0; width: 100%; top: 100px;
    display: flex; align-items: center; justify-content: center;
  }
  .back-brand__mark { width: 46px; height: 46px; background: var(--accent); margin-right: 18px; }
  .back-brand__name { font-size: 46px; font-weight: 700; color: var(--ink); letter-spacing: -1px; }
  .back-web {
    position: absolute; left: 0; width: 100%; top: 232px; text-align: center;
    font-size: 13px; letter-spacing: 1.8px; color: var(--ink);
  }
</style>
</head>
<body>
<main class="canvas">
  <section class="card card--front" aria-label="Business card front">
    <div class="edge-strip"></div>
    <div class="brand">
      <span class="brand__mark"></span>
      <span class="brand__name">Varentoria</span>
    </div>
    <p class="tagline">ASSESSING EXECUTIVE PROMISE</p>
    <div class="person">
      <p class="person__name">DEREK HANFORD</p>
      <p class="person__role">Prime Capacity Officer</p>
    </div>
    <ul class="contact">
      <li><span class="contact__label">P:</span> 1300 582 714</li>
      <li><span class="contact__label">M:</span> 0412 637 258</li>
      <li><span class="contact__label">E:</span> derek.hanford@varentoria-example.com.au</li>
    </ul>
    <ul class="address">
      <li>Level 17, Marlow Tower</li>
      <li>7 Marlow Square, Sydney</li>
      <li>NSW 2090 Australia</li>
    </ul>
    <p class="website">www.VARENTORIA-EXAMPLE.com.au</p>
  </section>

  <section class="card card--back" aria-label="Business card back">
    <div class="back-brand">
      <span class="back-brand__mark"></span>
      <span class="back-brand__name">Varentoria</span>
    </div>
    <p class="back-web">VARENTORIA-EXAMPLE.COM.AU</p>
  </section>
</main>
</body>
</html>
```